A website for a Maltese Law Firm

Our law firm needs a website to further its business. The site should have a simple yet effective design. We would need the following sections: About us, Practice Areas, About Malta, Contact. These should be further split as follows:

About us: Our firm, Our values, What others say, Offices

Practice Areas: Crimimal, Citizenship & Residence, Sovereign Patron Pathway, Criminal Defence, Civil Litigation, Arbitration and ADR, Commercial and Corporate, Media Law.

About Malta: just one section.

Contact: Just one section

We would also need a news feed at the front of the site to include latest news regarding our cases.

At the bottom we need a section for our Terms and a Privacy Statement.

Our logo is being attached.

Target Market(s)

All clients looking for legal assistance in Malta

Industry/Entity Type

Legal

Coding

Coded - Design and coding required

Number of Pages Required

1 page

Requirements
Must have
• It must be simple yet striking.

```html
<!DOCTYPE html>
<html lang="en">
<head>
<meta charset="utf-8">
<title>Zammit &amp; Grech Advocates</title>
<link rel="stylesheet" href="https://fonts.googleapis.com/css2?family=Open+Sans:wght@400;600;700&display=swap">
<style>
:root{
  --ink:#1c1c1c;
  --dark:#1e1e1e;
  --nav:#232323;
  --footer:#333333;
  --muted:#8a8a8a;
  --light:#f2f2f2;
  --panel:#ebebeb;
  --white:#ffffff;
  --line:#4a4a4a;
}
*{box-sizing:border-box;margin:0;padding:0}
html,body{width:800px;height:1200px;overflow:hidden;background:var(--white)}
body{font-family:"Open Sans",Arial,sans-serif;color:var(--ink);position:relative}
.abs{position:absolute}

/* header */
.header-phone{left:88px;top:26px;font-size:8px;display:flex;align-items:center;gap:3px}
.brand{left:0;width:800px;top:14px;text-align:center}
.brand-name{font-size:19px;font-weight:400;letter-spacing:1.5px;text-transform:uppercase;border-top:1px solid var(--ink);border-bottom:1px solid var(--ink);display:inline-block;padding:2px 6px;line-height:22px}
.header-social{right:88px;top:25px;display:flex;gap:10px;font-size:8px;font-weight:600;color:#555}
.main-nav{left:88px;top:62px;width:624px;height:26px;background:var(--nav);display:flex;justify-content:center;align-items:center;gap:18px;z-index:2}
.main-nav span{color:var(--white);font-size:6.5px;text-transform:uppercase}

/* hero */
.hero{left:0;top:76px;width:800px;height:293px;background:linear-gradient(90deg,#cfc6bb 0%,#8a6b4b 35%,#5a3a22 55%,#8d6444 80%,#b89170 100%)}
.welcome{left:491px;top:165px;width:220px;height:115px;background:rgba(240,232,222,.88);padding:12px 10px;text-align:right}
.welcome h1{font-size:21px;font-weight:700;line-height:24px;color:#111}
.welcome h2{font-size:12.5px;font-weight:400;text-transform:uppercase;line-height:16px}
.welcome p{font-size:6.5px;line-height:11.5px;margin-top:8px;color:#222}
.slider-dots{left:374px;top:343px;width:52px;height:12px;border-radius:6px;background:rgba(0,0,0,.35);display:flex;justify-content:center;align-items:center;gap:5px}
.slider-dots i{width:5px;height:5px;border-radius:50%;background:var(--white)}
.slider-dots i:first-child{background:none;border:1px solid var(--white)}

/* practice areas */
.practice{left:0;top:369px;width:800px;height:347px;background:var(--dark)}
.practice h3{position:absolute;left:0;width:800px;top:21px;text-align:center;color:var(--white);font-size:16px;font-weight:600}
.area{position:absolute;width:146px;height:125px;background:var(--white)}
.area-photo{height:92px}
.area-label{height:33px;display:flex;align-items:center;justify-content:center;text-align:center;font-size:10px;font-weight:600;text-transform:uppercase;line-height:11.5px;padding:0 6px}

/* news */
.news-title{left:88px;top:740px;font-size:16px;font-weight:400}
.news-arrow{top:741px;width:17px;height:18px;border:1px solid #ccc;display:flex;align-items:center;justify-content:center}
.news-card{top:773px;width:198px;height:89px;background:var(--light);border-top:2px solid var(--ink);padding:10px 10px;display:flex;gap:8px}
.news-date{text-align:center;width:18px;flex:none}
.news-date small{display:block;font-size:6.5px}
.news-date b{display:block;font-size:12px;font-weight:400}
.news-body h4{font-size:8.5px;font-weight:400;line-height:11.5px;color:#333}
.news-body p{font-size:5.6px;line-height:9.5px;color:var(--muted);margin-top:4px;text-align:justify}

/* contact */
.map{left:0;top:896px;width:400px;height:165px;background:linear-gradient(135deg,#d8d8d8,#c4c4c4 50%,#dcdcdc)}
.contact{left:400px;top:896px;width:400px;height:165px;background:var(--panel)}
.contact h3{position:absolute;left:33px;top:18px;font-size:16px;font-weight:400;color:#333}
.field{position:absolute;width:121px;height:24px;background:var(--white);border:1px solid #ddd;font-size:7.5px;color:#777;padding-left:11px;display:flex;align-items:center}
.submit{position:absolute;width:121px;height:24px;background:var(--nav);color:var(--white);font-size:8px;display:flex;align-items:center;justify-content:center;text-transform:uppercase}

/* footer */
.footer{left:0;top:1061px;width:800px;height:139px;background:var(--footer);color:#cfcfcf}
.footer-info{position:absolute;top:15px;font-size:7.5px;display:flex;align-items:center;gap:6px}
.footer-social{position:absolute;right:88px;top:16px;display:flex;gap:10px;font-size:7px;font-weight:600}
.footer-rule{position:absolute;left:88px;top:41px;width:624px;height:1px;background:var(--line)}
.footer-links{position:absolute;left:88px;top:55px;font-size:6.5px}
.footer-copy{position:absolute;left:88px;top:72px;font-size:6.5px}
.footer-brand{position:absolute;right:88px;top:60px;font-size:11.5px;letter-spacing:1px;text-transform:uppercase;color:#777;border-bottom:1px solid #555;line-height:15px}
.footer-privacy{position:absolute;left:88px;top:104px;width:624px;font-size:6px;line-height:10px;color:#9a9a9a}
</style>
</head>
<body>

<div class="abs header-phone">
  <svg width="8" height="8" viewBox="0 0 10 10"><path d="M2 1l2 2-1 1.2c.6 1.3 1.5 2.2 2.8 2.8L7 6l2 2-1.2 1.5C4.5 9 1 5.5.5 2.2z" fill="#1c1c1c"/></svg>
  <span>CALL US ON : (356) 2100 4455</span>
</div>
<div class="abs brand"><span class="brand-name">Zammit &amp; Grech</span></div>
<div class="abs header-social"><span>FB</span><span>TW</span><span>IN</span></div>

<div class="abs hero" role="img" aria-label="Photo of a smiling lawyer in a suit seated before law library bookshelves"></div>
<nav class="abs main-nav">
  <span>Home</span><span>About Us</span><span>Practice Areas</span><span>About Malta</span><span>Contact Us</span>
</nav>
<div class="abs welcome">
  <h1>WELCOME TO</h1>
  <h2>Zammit &amp; Grech</h2>
  <p>Maecenas dapibus odio eget lectus sodales sollicitudin. Donec iaculis pulvinar porttitor. Donec scelerisque ipsum eget enim feugiat, ac aliquam justo auctor. Maecenas quis massa libero. Donec sodales et dolor ornare sodales.</p>
</div>
<div class="abs slider-dots"><i></i><i></i><i></i><i></i></div>

<section class="abs practice">
  <h3>OUR PRACTICE AREAS</h3>
  <div class="area" style="left:88px;top:53px"><div class="area-photo" role="img" aria-label="Handcuffed hands" style="background:linear-gradient(135deg,#6e6e6e,#3c3c3c)"></div><div class="area-label">Criminal</div></div>
  <div class="area" style="left:247px;top:53px"><div class="area-photo" role="img" aria-label="Passport and gavel on a flag" style="background:linear-gradient(135deg,#2c3a5e,#8a8fa8 60%,#c8c8d0)"></div><div class="area-label">Citizenship &amp; Residence</div></div>
  <div class="area" style="left:406px;top:53px"><div class="area-photo" role="img" aria-label="Advisers meeting with clients" style="background:linear-gradient(135deg,#d9d4cc,#8c7a68 60%,#e6e2dc)"></div><div class="area-label">Sovereign Patron Pathway</div></div>
  <div class="area" style="left:566px;top:53px"><div class="area-photo" role="img" aria-label="Gavel beside handcuffs" style="background:linear-gradient(135deg,#5a3a24,#8a6446 50%,#b8b0a8)"></div><div class="area-label">Criminal Defence</div></div>
  <div class="area" style="left:88px;top:192px"><div class="area-photo" role="img" aria-label="Wooden letter blocks on a table" style="background:linear-gradient(135deg,#5e5a54,#c9b89a 50%,#6a655e)"></div><div class="area-label">Civil Litigation</div></div>
  <div class="area" style="left:247px;top:192px"><div class="area-photo" role="img" aria-label="Hand signing a document with a magnifier" style="background:linear-gradient(180deg,#5a3a28,#a88a6c 55%,#e0dad2)"></div><div class="area-label">Arbitration and ADR</div></div>
  <div class="area" style="left:406px;top:192px"><div class="area-photo" role="img" aria-label="Business team around a laptop" style="background:linear-gradient(135deg,#e6eef2,#3e4450 55%,#dfe6ea)"></div><div class="area-label">Commercial and Corporate</div></div>
  <div class="area" style="left:566px;top:192px"><div class="area-photo" role="img" aria-label="Person in a suit holding up a card" style="background:linear-gradient(90deg,#9aa0a4,#2a2a2a 50%,#a4aaae)"></div><div class="area-label">Media Law</div></div>
</section>

<h3 class="abs news-title">Latest News</h3>
<div class="abs news-arrow" style="left:676px"><svg width="5" height="8" viewBox="0 0 5 8"><path d="M4 1L1 4l3 3" fill="none" stroke="#999"/></svg></div>
<div class="abs news-arrow" style="left:696px"><svg width="5" height="8" viewBox="0 0 5 8"><path d="M1 1l3 3-3 3" fill="none" stroke="#999"/></svg></div>

<article class="abs news-card" style="left:88px">
  <div class="news-date"><small>Jun</small><b>08</b></div>
  <div class="news-body"><h4>Donec dolor tortor, aliquam quis nulla nec, elementum finibus</h4><p>Phasellus nec sapien vitae nulla bibendum commodo. Morbi suscipit molestie dolor non aliquam. Donec id fringilla tortor. Praesent in feugiat ligula, sit amet commodo risus.</p></div>
</article>
<article class="abs news-card" style="left:301px">
  <div class="news-date"><small>Jun</small><b>08</b></div>
  <div class="news-body"><h4>Donec dolor tortor, aliquam quis nulla nec, elementum finibus</h4><p>Phasellus nec sapien vitae nulla bibendum commodo. Morbi suscipit molestie dolor non aliquam. Donec id fringilla tortor. Praesent in feugiat ligula, sit amet commodo risus.</p></div>
</article>
<article class="abs news-card" style="left:514px">
  <div class="news-date"><small>Jun</small><b>08</b></div>
  <div class="news-body"><h4>Donec dolor tortor, aliquam quis nulla nec, elementum finibus</h4><p>Phasellus nec sapien vitae nulla bibendum commodo. Morbi suscipit molestie dolor non aliquam. Donec id fringilla tortor. Praesent in feugiat ligula, sit amet commodo risus.</p></div>
</article>

<div class="abs map" role="img" aria-label="Grey world map"></div>
<section class="abs contact">
  <h3>Contact Us</h3>
  <div class="field" style="left:33px;top:45px">First Name</div>
  <div class="field" style="left:161px;top:45px">Last Name</div>
  <div class="field" style="left:33px;top:77px">Phone</div>
  <div class="field" style="left:161px;top:77px">Email</div>
  <div class="field" style="left:33px;top:109px">City</div>
  <div class="submit" style="left:161px;top:109px">Submit</div>
</section>

<footer class="abs footer">
  <div class="footer-info" style="left:88px">
    <svg width="7" height="9" viewBox="0 0 7 10"><path d="M3.5 0A3.5 3.5 0 0 0 0 3.5C0 6 3.5 10 3.5 10S7 6 7 3.5A3.5 3.5 0 0 0 3.5 0zm0 5a1.5 1.5 0 1 1 0-3 1.5 1.5 0 0 1 0 3z" fill="#cfcfcf"/></svg>
    <span>12 Merchant Lane, Valletta VLT 1100</span>
  </div>
  <div class="footer-info" style="left:346px">
    <svg width="8" height="8" viewBox="0 0 10 10"><path d="M2 1l2 2-1 1.2c.6 1.3 1.5 2.2 2.8 2.8L7 6l2 2-1.2 1.5C4.5 9 1 5.5.5 2.2z" fill="#cfcfcf"/></svg>
    <span>Call Now: (356) 2100 4455</span>
  </div>
  <div class="footer-info" style="left:498px">
    <svg width="10" height="8" viewBox="0 0 10 8"><rect width="10" height="8" fill="#cfcfcf"/><path d="M0 0l5 4 5-4" fill="none" stroke="#333"/></svg>
    <span>Email:&nbsp; info@zgadvocates.example</span>
  </div>
  <div class="footer-social"><span>FB</span><span>TW</span><span>IN</span></div>
  <div class="footer-rule"></div>
  <div class="footer-links">Home &nbsp;|&nbsp; About us &nbsp;|&nbsp; Practice Areas &nbsp;|&nbsp; About Malta &nbsp;|&nbsp; Contact us &nbsp;|&nbsp; Terms and Conditions</div>
  <div class="footer-copy">Copyright &copy; 2016 ZG Advocates.&nbsp; All rights reserved.</div>
  <div class="footer-brand">Zammit &amp; Grech</div>
  <p class="footer-privacy">Privacy Statement : Sed gravida varius neque, quis semper tortor ultricies quis. Quisque quam ipsum, mattis non nisl a, facilisis convallis odio. In hac habitasse platea dictumst. In commodo nisl blandit odio euis mod laoreet. Nam mattis venenatis urna, in interdum nunc. Aliquam quis tortor metus.</p>
</footer>

</body>
</html>
```